Corporate brochure design 4 pages

Hi,

We are a real estate company based in Europe.

We have almost finalized a rebranding.

We are developing a brand book guidelines (still on working process) to help you undertstand the look and feel of our new CI. I would like to receive proposals of design for a corporate brochure template. I need to receive the Indesign files with full ownership rights to be able to adapt all our documentation with this template.
Regarding the images, you can take gabaris on www.pelvarimages.example. I will be able to take them afterwards.

There will be 4 pages. you will receive the 4 pages on pdf for your consideration with our (almost) actual layout.

- 1st page: cover
- 2nd page: company presentation in french and english
- 3rd page: some market data + graph
- 4th page: 2 retail centers presentation.

In the template, i need to have:
- the paragraph styles in order
- 2 different masters with top/bottom/page number aso.

Please feel free to ask any other questions.

best regards,
Updates

I would like to precise tha t we are active on the commercial real estate sector:

- office transactions (rent /sales)
- property management of administrative and business buildings
- Valuation of properties
- Capital markets (investment advices for selling building)

Industry/Entity Type

Real Estate

Colors

Designer to choose colors to be used in the design.

```html
<!DOCTYPE html>
<html lang="fr">
<head>
<meta charset="utf-8">
<title>Orvelle Partners – A Propos De Nous</title>
<link href="https://fonts.googleapis.com/css2?family=Arimo:wght@400;700&display=swap" rel="stylesheet">
<style>
  :root{
    --orange:#ee6a21;
    --ink:#1d1d1b;
    --text:#3c3c3b;
    --muted:#555;
    --rule:#9a9a9a;
    --frame:#8c8c8c;
    --paper:#ffffff;
    --photo-a:#7c8a92;
    --photo-b:#c9d0d3;
    --photo-c:#3a3f45;
  }
  *{box-sizing:border-box;margin:0;padding:0}
  html,body{width:873px;height:1200px;overflow:hidden;background:var(--paper)}
  body{font-family:"Arimo",Arial,sans-serif;color:var(--text);position:relative}
  .page{position:absolute;left:26px;top:24px;width:817px;height:1151px;border:1px solid var(--frame)}
  .team-photo{position:absolute;left:26px;top:24px;width:817px;height:549px;
    background:linear-gradient(180deg,var(--photo-b) 0%,var(--photo-a) 45%,var(--photo-c) 100%)}
  .caption{position:absolute;left:76px;top:584px;font-size:11.5px;color:var(--muted)}
  .page-title{position:absolute;left:76px;top:632px;font-size:30px;font-weight:700;color:var(--orange);letter-spacing:-0.3px}
  .column{position:absolute;top:704px}
  .column.fr{left:76px;width:344px}
  .column.en{left:462px;width:333px}
  .tab{display:inline-block;background:var(--orange);color:#fff;font-size:17px;height:32px;line-height:33px;padding:0 14px;border-radius:0 8px 0 0}
  .lead{margin-top:16px;font-weight:700;color:var(--ink);font-size:12.6px;line-height:17px;letter-spacing:-0.35px}
  .body{margin-top:14px;font-size:13px;line-height:17.5px;text-align:justify;hyphens:auto}
  .en .body{margin-top:10px}
  .folio{position:absolute;left:76px;top:1111px;font-size:15px;font-weight:700;color:var(--ink)}
  .folio-rule{position:absolute;left:104px;top:1120px;width:508px;height:1px;background:var(--rule)}
  .brand{position:absolute;left:628px;top:1092px;display:flex;align-items:center;gap:8px}
  .brand-mark{width:12px;height:12px;background:var(--orange)}
  .brand-name{font-size:34px;font-weight:700;color:var(--ink);letter-spacing:-0.5px}
</style>
</head>
<body>
  <div class="page"></div>
  <div class="team-photo" role="img" aria-label="Photo of the four partners in dark suits in a glass-walled office lobby"></div>
  <p class="caption">Julien Marceau, Olivier Dastré, Paul Wenderlin, Tomas Greyling</p>

  <h1 class="page-title">A Propos De Nous/About Us</h1>

  <section class="column fr">
    <span class="tab">Une Équipe</span>
    <p class="lead">Proposer des services de qualité répondant parfaitement à vos attentes est notre ambition. Elle est partagée par tous les membres de notre équipe.</p>
    <p class="body">Notre connaissance du marché luxembourgeois, nos compétences et notre engagement dans les missions qui nous sont confiées font de Orvelle Partners l’acteur majeur de l’immobilier d’entreprise au Grand-Duché. Nous sommes fiers de cette position et nous travaillons tous les jours pour la conserver.</p>
    <p class="body">Viser l’excellence suppose de savoir améliorer sans cesse nos prestations pour répondre le plus précisément à vos besoins. Venez nous consulter, vous constaterez que nos collaborateurs prennent le temps de vous écouter pour bien comprendre votre demande. Leur professionnalisme, leur savoir-faire et leur mobilisation nous permettront de trouver la solution.</p>
  </section>

  <section class="column en" lang="en">
    <span class="tab">A Team</span>
    <p class="lead">Our ambition is to offer quality services that perfectly meet your expectations. This ambition is shared by all members of the team.</p>
    <p class="body">Thanks to our knowledge of the Luxembourg market, our skills and our commitment to the missions entrusted to us, Orvelle Partners is the undisputed leader in commercial real estate in the Grand Duchy. We are proud of this position and work hard to deserve it every day.</p>
    <p class="body">Targeting excellence means the constant improvement of our services in order to more accurately meet your needs. When you meet with us, you will find that our employees take the necessary time to listen to you and to correctly understand your need. Their professionalism, know-how and mobilisation will ensure that we find the right solution.</p>
  </section>

  <span class="folio">02</span>
  <div class="folio-rule"></div>
  <div class="brand">
    <span class="brand-mark"></span>
    <span class="brand-name">HALDEN</span>
  </div>
</body>
</html>
```